Corvane Capital Business Cards

These are professional business cards that are for my family office.
Put fake emails and phone numbers as of now until I finalize those components. This family office controls my families investments, assets, and future. The cards should be professional.
..
.
.
.
I just uploaded another variation of a logo I would like to see as a business card to I am inbeteen which logo to use

Target Market(s)

business

Industry/Entity Type

business

Contact Information for Business Card

Professional, wealth related, finance related.

Requirements
Must have
• Logo

```html
<!DOCTYPE html>
<html lang="en">
<head>
<meta charset="utf-8">
<title>Corvane Capital Business Cards</title>
<link rel="stylesheet" href="https://fonts.googleapis.com/css2?family=Poppins:wght@400;500;600;700&display=swap">
<style>
  :root {
    --navy: #171d2b;
    --white: #ffffff;
    --grey: #a8a8a8;
    --backdrop: #e3e6e8;
  }
  * { box-sizing: border-box; margin: 0; padding: 0; }
  html, body { width: 1200px; height: 960px; overflow: hidden; }
  body {
    background: var(--backdrop);
    font-family: "Poppins", sans-serif;
    position: relative;
  }
  .card {
    position: absolute;
    top: 105px;
    width: 429px;
    height: 749px;
    border-radius: 28px;
    overflow: hidden;
    background: var(--navy);
  }
  .card--front { left: 142px; }
  .card--back { left: 631px; }

  /* front */
  .front-ring {
    position: absolute;
    left: 86px; top: 277px;
    width: 194px; height: 194px;
    border: 4px solid var(--white);
    border-radius: 50%;
  }
  .front-name {
    position: absolute;
    left: 322px; top: 377px;
    transform: translate(-50%, -50%) rotate(-90deg);
    white-space: nowrap;
    color: var(--white);
    font-weight: 600;
    font-size: 30px;
    letter-spacing: 1.5px;
    text-transform: uppercase;
  }

  /* back */
  .back-top {
    position: absolute;
    left: 0; top: 0;
    width: 100%; height: 262px;
    background: var(--white);
  }
  .back-name {
    position: absolute;
    top: 50px; left: 0; width: 100%;
    text-align: center;
    color: var(--navy);
    font-weight: 600;
    font-size: 29px;
    letter-spacing: 1px;
    text-transform: uppercase;
  }
  .back-ring {
    position: absolute;
    left: 111px; top: 161px;
    width: 212px; height: 212px;
    border-radius: 50%;
    background: var(--white);
    border: 5px solid var(--navy);
    box-shadow: 0 0 0 3px var(--white);
  }
  .person {
    position: absolute;
    top: 408px; left: 0; width: 100%;
    text-align: center;
    color: var(--grey);
    font-size: 37px;
    line-height: 1.2;
    letter-spacing: 1px;
  }
  .person__first { font-weight: 600; }
  .person__last { font-weight: 400; }
  .role {
    position: absolute;
    top: 453px; left: 0; width: 100%;
    text-align: center;
    color: var(--white);
    font-weight: 500;
    font-size: 18px;
    letter-spacing: 0.5px;
  }
  .divider {
    position: absolute;
    left: 0;
    width: 429px; height: 34px;
  }
  .divider--contact { top: 491px; }
  .divider--address { top: 626px; }
  .contact-list, .address {
    position: absolute;
    left: 0; width: 100%;
    text-align: center;
    color: var(--white);
    font-size: 19.5px;
    line-height: 27.5px;
    letter-spacing: 0.6px;
    list-style: none;
  }
  .contact-list { top: 532px; }
  .address { top: 667px; font-style: normal; }
</style>
</head>
<body>

<section class="card card--front" aria-label="Card front">
  <div class="front-ring"></div>
  <div class="front-name">Corvane Capital</div>
</section>

<section class="card card--back" aria-label="Card back">
  <div class="back-top"></div>
  <div class="back-name">Corvane Capital</div>
  <div class="back-ring"></div>

  <div class="person"><span class="person__first">Petra</span> <span class="person__last">Novakova</span></div>
  <div class="role">Founder &amp; CEO</div>

  <svg class="divider divider--contact" viewBox="0 0 429 34" aria-hidden="true">
    <g stroke="#a8a8a8" stroke-width="1.5">
      <line x1="18" y1="17" x2="152" y2="17"/>
      <line x1="277" y1="17" x2="411" y2="17"/>
    </g>
    <g fill="#a8a8a8">
      <circle cx="176" cy="17" r="15"/><circle cx="214" cy="17" r="15"/><circle cx="252" cy="17" r="15"/>
    </g>
    <path d="M170 10c1-1 2-1 2.6 0l1.8 2.6c.5.7.3 1.5-.3 2l-1 .8c.8 1.8 2.2 3.3 4 4.2l.8-1c.5-.6 1.3-.7 2-.3l2.6 1.7c.9.6.9 1.7 0 2.6l-1.2 1.2c-4.5 1.3-12.6-6.6-11.4-11.5z" fill="#ffffff"/>
    <g fill="none" stroke="#ffffff" stroke-width="1.6" stroke-linejoin="round">
      <rect x="206" y="11" width="16" height="12" rx="1.5"/>
      <polyline points="206.5,12 214,18 221.5,12"/>
    </g>
    <g fill="none" stroke="#ffffff" stroke-width="1.5">
      <circle cx="252" cy="17" r="8"/>
      <ellipse cx="252" cy="17" rx="3.5" ry="8"/>
      <line x1="244" y1="17" x2="260" y2="17"/>
    </g>
  </svg>

  <ul class="contact-list">
    <li>(512) 404-1187</li>
    <li>info@yourwebsite.com</li>
    <li>www.yourwebsite.com</li>
  </ul>

  <svg class="divider divider--address" viewBox="0 0 429 34" aria-hidden="true">
    <g stroke="#a8a8a8" stroke-width="1.5">
      <line x1="18" y1="17" x2="190" y2="17"/>
      <line x1="239" y1="17" x2="411" y2="17"/>
    </g>
    <circle cx="214" cy="17" r="15" fill="#a8a8a8"/>
    <g fill="none" stroke="#ffffff" stroke-width="1.6">
      <path d="M214 26c-3.5-4.5-6-7.5-6-11a6 6 0 0 1 12 0c0 3.5-2.5 6.5-6 11z"/>
      <circle cx="214" cy="15" r="2.2"/>
    </g>
  </svg>

  <address class="address">
    1840 Linden Ave. Suite 300<br>
    Austin, TX 78704
  </address>
</section>

</body>
</html>
```